Design a Website for an IT Support Company

We are an IT support company that provides commercial IT support and services to small and medium sized businesses. We are in need of a website to be developed for our business.
We would like to work with someone who is either familiar with the IT field, or has developed a website for an IT support company in the past.
Some examples of designs/layouts that we like:
https://www.veldaworks.example/
http://www.marsbyquill.example/
http://817kq.example/
http://www.olbenstructures.example/
http://www.bykq.example/
I have attached a word document that gives a menu system/page layout format that we would like for our website as well as branch office phone numbers. Our logo is also attached that you can use for your design purposes. We currently do not have copy produced for all of the pages outlined in the word document, but would get this done during the project with the selected designer.
We would like the website to be SEO friendly & fully responsive. We would prefer a Wordpress format, however, we are open to HTML formats as well.

```html
<!DOCTYPE html>
<html lang="en">
<head>
<meta charset="utf-8">
<title>Swiftline IT — Managed IT Support</title>
<link href="https://fonts.googleapis.com/css2?family=Open+Sans:wght@400;600;700&display=swap" rel="stylesheet">
<style>
:root{
  --blue:#0a74c2;
  --blue-dark:#075e9e;
  --ink:#1d1d1d;
  --muted:#8a8a8a;
  --band:#f4f4f4;
  --footer:#3a3a3a;
  --white:#ffffff;
}
*{box-sizing:border-box;margin:0;padding:0}
html,body{width:782px;height:1200px;overflow:hidden;background:var(--white)}
body{font-family:"Open Sans",Arial,sans-serif;color:var(--ink);position:relative}
.abs{position:absolute}

/* header */
.site-header{position:absolute;left:0;top:0;width:782px;height:88px}
.brand{left:86px;top:30px;display:flex;align-items:center;gap:8px}
.brand-dot{width:22px;height:22px;border-radius:50%;background:var(--blue)}
.brand-name{font-size:20px;font-weight:600;color:var(--ink);letter-spacing:.2px}
.header-phone{right:87px;top:17px;font-size:14px;display:flex;align-items:center;gap:5px;color:var(--ink)}
.main-nav{right:87px;top:55px;display:flex;gap:22px;font-size:8.5px;letter-spacing:.2px}
.main-nav a{color:var(--ink);text-decoration:none}
.main-nav a.active{color:var(--blue)}

/* hero */
.hero{left:0;top:88px;width:782px;height:312px;
  background:linear-gradient(100deg,#c9cdd2 0%,#9aa4ae 30%,#5b7590 55%,#8a9aa8 75%,#c7c6c2 100%)}
.hero-caption{left:86px;top:86px;font-size:15.5px;line-height:19px;color:#111;font-weight:400}
.hero-arrow{top:146px}
.hero-arrow.prev{left:15px}
.hero-arrow.next{right:15px}

/* services */
.service{top:452px;width:194px;height:194px;background:var(--blue);color:var(--white);text-align:center}
.service .icon{position:absolute;left:0;right:0;top:20px;height:48px;display:flex;justify-content:center}
.service h3{position:absolute;left:0;right:0;top:76px;font-size:15.5px;font-weight:700;letter-spacing:.4px}
.service p{position:absolute;left:18px;right:18px;top:101px;font-size:7px;line-height:12.5px;color:#d8e8f5}
.service .btn{position:absolute;left:65px;top:146px;width:64px;height:26px;border:1px solid #d8e8f5;
  font-size:6.5px;line-height:24px;color:var(--white);text-decoration:none}

/* why */
.why{left:0;top:697px;width:782px;height:317px;background:var(--band)}
.section-title{left:0;width:782px;text-align:center;font-size:15px;font-weight:700;color:var(--blue);letter-spacing:.3px}
.feature{width:280px}
.feature .ficon{position:absolute;left:0;top:0;width:18px;height:18px}
.feature h4{position:absolute;left:28px;top:0;font-size:10.5px;font-weight:400;color:var(--ink);white-space:nowrap}
.feature p{position:absolute;left:28px;top:17px;width:260px;font-size:6.3px;line-height:10.5px;color:var(--muted)}

/* contact */
.office{top:1076px}
.office .city{font-size:8.5px;color:var(--ink)}
.office .num{font-size:12.5px;color:var(--ink);margin-top:1px}

/* footer */
.site-footer{left:0;top:1137px;width:782px;height:63px;background:var(--footer);color:#d0d0d0}
.footer-nav{left:86px;top:18px;font-size:6.5px}
.footer-nav span{margin:0 5px}
.copyright{left:86px;top:36px;font-size:6.5px}
.social{right:87px;top:23px;display:flex;gap:5px}
.social i{display:block;width:16px;height:16px;border-radius:50%;background:#6e86a4}
</style>
</head>
<body>

<header class="site-header">
  <div class="abs brand"><span class="brand-dot"></span><span class="brand-name">Swiftline IT</span></div>
  <div class="abs header-phone">
    <svg width="11" height="11" viewBox="0 0 24 24"><path fill="#1d1d1d" d="M6.6 10.8c1.4 2.8 3.8 5.1 6.6 6.6l2.2-2.2c.3-.3.7-.4 1-.2 1.1.4 2.3.6 3.6.6.6 0 1 .4 1 1V20c0 .6-.4 1-1 1C10.6 21 3 13.4 3 4c0-.6.4-1 1-1h3.5c.6 0 1 .4 1 1 0 1.3.2 2.5.6 3.6.1.3 0 .7-.2 1z"/></svg>
    555-210-4400
  </div>
  <nav class="abs main-nav">
    <a class="active" href="#">HOME</a><a href="#">SERVICES</a><a href="#">WHY SWIFTLINE IT</a><a href="#">CONTACT</a>
  </nav>
</header>

<section class="abs hero" role="img" aria-label="Photo of two IT technicians looking at a monitor with code in an office">
  <h1 class="abs hero-caption">Phasellus nisl est<br>condimentum vitae faucibus</h1>
  <svg class="abs hero-arrow prev" width="12" height="20" viewBox="0 0 12 20"><path d="M10 2 2 10l8 8" fill="none" stroke="#555" stroke-width="2"/></svg>
  <svg class="abs hero-arrow next" width="12" height="20" viewBox="0 0 12 20"><path d="M2 2l8 8-8 8" fill="none" stroke="#555" stroke-width="2"/></svg>
</section>

<article class="abs service" style="left:86px">
  <div class="icon"><svg width="46" height="46" viewBox="0 0 46 46" fill="none" stroke="#fff" stroke-width="1.6"><path d="M9 4h24v30H9z"/><path d="M14 11h14M14 16h14M14 21h10"/><path d="M3 14h9l3 4h18l-5 24H3z"/></svg></div>
  <h3>DATA</h3>
  <p>Integer eu massa lacinia, lacinia nulla non, volutpat purus. Sed libero felis, vestibulum et dolor eget, lacinia aliquet neque.</p>
  <a class="btn" href="#">Read more</a>
</article>
<article class="abs service" style="left:294px">
  <div class="icon"><svg width="68" height="46" viewBox="0 0 68 46" fill="none" stroke="#fff" stroke-width="1.8"><path d="M16 42h38a12 12 0 0 0 1-24 18 18 0 0 0-34-4A14 14 0 0 0 16 42z"/></svg></div>
  <h3>CLOUD</h3>
  <p>Integer eu massa lacinia, lacinia nulla non, volutpat purus. Sed libero felis, vestibulum et dolor eget, lacinia aliquet neque.</p>
  <a class="btn" href="#">Read more</a>
</article>
<article class="abs service" style="left:501px">
  <div class="icon"><svg width="46" height="46" viewBox="0 0 46 46" fill="none" stroke="#fff" stroke-width="1.6"><path d="M6 4l8-2 6 11-5 4c3 7 8 12 15 15l4-5 11 6-2 8c-20 0-37-17-37-37z"/></svg></div>
  <h3>VOICE</h3>
  <p>Integer eu massa lacinia, lacinia nulla non, volutpat purus. Sed libero felis, vestibulum et dolor eget, lacinia aliquet neque.</p>
  <a class="btn" href="#">Read more</a>
</article>

<section class="abs why">
  <h2 class="abs section-title" style="top:50px">WHY SWIFTLINE IT</h2>

  <div class="abs feature" style="left:86px;top:96px">
    <svg class="ficon" viewBox="0 0 18 18" fill="#1d1d1d"><circle cx="4" cy="5" r="2.3"/><circle cx="14" cy="5" r="2.3"/><circle cx="9" cy="7" r="2.8"/><path d="M0 13c0-3 2-4 4-4s3 1 3 1H0zM11 10s1-1 3-1 4 1 4 4h-7zM4 16c0-4 2-6 5-6s5 2 5 6z"/></svg>
    <h4>Proin a dolor mauris</h4>
    <p>Phasellus nisl est, condimentum vitae faucibus in, sollicitudin vel metus. Nunc sit amet consequat risus. Curabitur ac elit leo.</p>
  </div>
  <div class="abs feature" style="left:442px;top:96px">
    <svg class="ficon" viewBox="0 0 18 18" fill="#1d1d1d"><path d="M6 3h6v2h5v11H1V5h5zM7 4v1h4V4z"/><rect x="1" y="9" width="16" height="1" fill="#f4f4f4"/></svg>
    <h4>Integer eu massa lacinia</h4>
    <p>Phasellus nisl est, condimentum vitae faucibus in, sollicitudin vel metus. Nunc sit amet consequat risus. Curabitur ac elit leo.</p>
  </div>
  <div class="abs feature" style="left:86px;top:164px">
    <svg class="ficon" viewBox="0 0 18 18"><circle cx="9" cy="9" r="7" fill="#1d1d1d"/><path d="M6 5c2 0 3 2 2 3s-3 0-3 2 2 2 2 4M12 5c-1 2 1 3 2 3" stroke="#f4f4f4" stroke-width="1.3" fill="none"/></svg>
    <h4>Sed libero felis, vestibulum et dolor</h4>
    <p>Phasellus nisl est, condimentum vitae faucibus in, sollicitudin vel metus. Nunc sit amet consequat risus. Curabitur ac elit leo.</p>
  </div>
  <div class="abs feature" style="left:442px;top:164px">
    <svg class="ficon" viewBox="0 0 18 18" fill="#1d1d1d"><circle cx="7" cy="10" r="4.5"/><circle cx="7" cy="10" r="1.6" fill="#f4f4f4"/><circle cx="14" cy="5" r="3"/><circle cx="14" cy="5" r="1" fill="#f4f4f4"/><circle cx="14" cy="14" r="2.3"/><circle cx="14" cy="14" r=".8" fill="#f4f4f4"/></svg>
    <h4>Aenean sed quam non sapien</h4>
    <p>Phasellus nisl est, condimentum vitae faucibus in, sollicitudin vel metus. Nunc sit amet consequat risus. Curabitur ac elit leo.</p>
  </div>
  <div class="abs feature" style="left:86px;top:232px">
    <svg class="ficon" viewBox="0 0 18 18" fill="#1d1d1d"><path d="M1 3h16v10H1zM2.5 4.5v7h13v-7z"/><path d="M7 13h4v2h2v1H5v-1h2z"/></svg>
    <h4>Praesent quis risus mi</h4>
    <p>Phasellus nisl est, condimentum vitae faucibus in, sollicitudin vel metus. Nunc sit amet consequat risus. Curabitur ac elit leo.</p>
  </div>
  <div class="abs feature" style="left:442px;top:232px">
    <svg class="ficon" viewBox="0 0 24 24" fill="#1d1d1d"><path d="M6.6 10.8c1.4 2.8 3.8 5.1 6.6 6.6l2.2-2.2c.3-.3.7-.4 1-.2 1.1.4 2.3.6 3.6.6.6 0 1 .4 1 1V20c0 .6-.4 1-1 1C10.6 21 3 13.4 3 4c0-.6.4-1 1-1h3.5c.6 0 1 .4 1 1 0 1.3.2 2.5.6 3.6.1.3 0 .7-.2 1z"/></svg>
    <h4>Aenean faucibus lacus ut mollis</h4>
    <p>Phasellus nisl est, condimentum vitae faucibus in, sollicitudin vel metus. Nunc sit amet consequat risus. Curabitur ac elit leo.</p>
  </div>
</section>

<h2 class="abs section-title" style="top:1049px">CONTACT US</h2>
<div class="abs office" style="left:86px"><div class="city">Main Number</div><div class="num">555-210-4400</div></div>
<div class="abs office" style="left:190px"><div class="city">Houston</div><div class="num">555-318-2270</div></div>
<div class="abs office" style="left:298px"><div class="city">San Antonio</div><div class="num">555-427-1830</div></div>
<div class="abs office" style="left:407px"><div class="city">Austin</div><div class="num">555-536-7050</div></div>
<div class="abs office" style="left:510px"><div class="city">Tulsa</div><div class="num">555-649-3310</div></div>
<div class="abs office" style="left:615px"><div class="city">Oklahoma City</div><div class="num">555-752-6620</div></div>

<footer class="abs site-footer">
  <div class="abs footer-nav">Home<span>|</span>Services<span>|</span>Why Swiftline IT<span>|</span>Contact</div>
  <div class="abs copyright">Copyright © 2017 Swiftline IT. All rights reserved.</div>
  <div class="abs social" aria-label="Social links"><i></i><i></i><i></i><i></i></div>
</footer>

</body>
</html>
```